Corporate Design - Immobilienverwaltungsgesellschaft
Zielgruppe
An- und Verkauf, Verwaltung und Vermietung von Immobilien
Zielgruppen: Immobilienspekulanten, Wohnungskäufer, Mieter, Vermieter
Aufgabenstellung
Wir suchen ein hochwertiges Design für eine in Gründung befindliche Gesellschaft mit beschränkter Haftung.
Diese wird aus 2 Gesellschaftern, Katrin und Torsten Fellmer bestehen.
Das Hauptziel der Gesellschaft wird der An- und Verkauf von Immobilien bis zu 1. Million Euro je Kaufobjekt sein
Mit dem Nachnamen der Gesellschafter kann auch gespielt werden, beispielsweise bei Abkürzungen. Die Bezeichnung F&F Verwaltungsgesellschaft mbH ist nicht zwingend, lediglich das Kürzel 'mbH' oder auch 'GmbH' ist aufgrund der Rechtsform der Gesellschaft zwingend aufzunehmen.
Diverse Designideen haben wir bereits vorliegen; hierauf kann aufgebaut werden, siehe Uploads
Unter anderem eine Anlehnung an die unter derselben Firmenadresse der Gesellschaft bestehende Rechtsanwaltskanzlei und deren Cooperate Design wäre eine Idee, jedoch keine zwingende Voraussetzung.

```html
<!DOCTYPE html>
<html lang="de">
<head>
<meta charset="utf-8">
<title>F&amp;F Verwaltungsgesellschaft mbH – Geschäftsausstattung</title>
<link href="https://fonts.googleapis.com/css2?family=Roboto:wght@400;500;700&family=Roboto+Condensed:wght@700&display=swap" rel="stylesheet">
<style>
  :root {
    --navy: #034379;
    --blue-text: #0b3f8c;
    --grey-bg: #e6e6e6;
    --grey-text: #8a8a8a;
    --grey-swoosh: #b3b3b3;
    --white: #ffffff;
    --accent: #29abe2;
  }
  * { margin: 0; padding: 0; box-sizing: border-box; }
  html, body { width: 1200px; height: 771px; overflow: hidden; }
  body {
    position: relative;
    background: var(--grey-bg);
    font-family: "Roboto", Arial, sans-serif;
  }

  /* Letterhead */
  .letterhead {
    position: absolute; left: 86px; top: 47px;
    width: 455px; height: 649px;
    background: var(--white);
    overflow: hidden;
  }
  .letterhead .brand {
    position: absolute; right: 30px; top: 40px;
    display: flex; align-items: center; gap: 6px;
  }
  .brand-dot {
    display: block; border-radius: 50%;
    background: var(--navy);
  }
  .brand-name {
    font-weight: 500; color: var(--navy); white-space: nowrap;
  }
  .letterhead .brand .brand-dot { width: 26px; height: 26px; }
  .letterhead .brand .brand-name { font-size: 11px; }
  .edge-bar {
    position: absolute; right: 1px; top: 41px;
    width: 3px; height: 166px; background: var(--navy);
  }
  .imprint {
    position: absolute; right: 23px; top: 83px;
    text-align: right; font-size: 6.6px; line-height: 8.6px;
  }
  .imprint dt { color: var(--blue-text); font-weight: 500; }
  .imprint dd { color: var(--grey-text); }
  .sender {
    position: absolute; left: 33px; top: 116px;
    font-size: 8px; font-weight: 500; color: var(--blue-text);
    text-decoration: underline;
  }
  .footer-wave {
    position: absolute; left: 0; top: 529px; width: 455px; height: 120px;
  }
  .footer-info {
    position: absolute; left: 15px; right: 14px; bottom: 10px;
    display: flex; align-items: baseline;
    font-family: "Roboto Condensed", Arial, sans-serif; font-weight: 700;
    color: var(--white); font-size: 7px;
  }
  .footer-info .sep {
    display: inline-block; width: 4px; height: 4px; border-radius: 50%;
    background: var(--accent); margin: 0 9px; transform: translateY(-1px);
  }
  .footer-info .web { margin-left: auto; font-size: 13px; }

  /* Business cards */
  .card {
    position: absolute; background: var(--white);
    display: flex; align-items: center; justify-content: center;
  }
  .card-front { left: 592px; top: 71px; width: 490px; height: 275px; }
  .card-front .brand { display: flex; align-items: center; gap: 10px; margin-left: -20px; margin-top: -10px; }
  .card-front .brand-dot { width: 62px; height: 62px; }
  .card-front .brand-name { font-size: 18px; }

  .card-back-dark { left: 591px; top: 406px; width: 246px; height: 276px; background: var(--navy); }
  .card-back-light { left: 837px; top: 406px; width: 245px; height: 276px; }
  .card-stack { display: flex; flex-direction: column; align-items: center; gap: 14px; }
  .card-stack .brand-dot { width: 78px; height: 78px; }
  .card-stack .brand-name { font-size: 12px; }
  .card-back-dark .brand-dot { background: var(--white); }
  .card-back-dark .brand-name { color: var(--white); }
</style>
</head>
<body>

<section class="letterhead" aria-label="Briefbogen">
  <div class="brand">
    <span class="brand-dot"></span>
    <span class="brand-name">F&amp;F Verwaltungsgesellschaft mbH</span>
  </div>
  <div class="edge-bar"></div>

  <dl class="imprint">
    <dt>Geschäftsführer:</dt>
    <dd>Katrin Fellmer, Torsten Fellmer</dd>
    <dd>Firmensitz</dd>
    <dt>Umsatzsteuer-Identifikationsnummer:</dt>
    <dd>xxxxxxxxxxxxxxxxxxxx</dd>
    <dt>Handelsregisternummer:</dt>
    <dd>xxxxxxxxxxxxxxxxxxxxxx</dd>
    <dt>Telefonnummer:</dt>
    <dd>xxxxxxxxxxxxxxx</dd>
    <dt>Fax:</dt>
    <dd>xxxxxxxxxxxxxxx</dd>
    <dt>Email:</dt>
    <dd>info@ff-verwaltung.de</dd>
  </dl>

  <p class="sender">F&amp;F Verwaltungsgesellschaft mbH</p>

  <svg class="footer-wave" viewBox="0 0 455 120" preserveAspectRatio="none" aria-hidden="true">
    <path d="M0 11 C110 52 260 68 455 58 L455 52 C290 66 140 64 0 31 Z" fill="var(--grey-swoosh)"/>
    <path d="M0 35 C140 70 300 74 455 56 L455 120 L0 120 Z" fill="var(--navy)"/>
  </svg>

  <div class="footer-info">
    <span>Bankinstitut : Talbank Lindenfeld</span>
    <span class="sep"></span>
    <span>IBAN : DE12 3456 0000 0012 3456 78</span>
    <span class="sep"></span>
    <span>BIC : TLBKDE51</span>
    <span class="web">www.f&amp;f.de</span>
  </div>
</section>

<section class="card card-front" aria-label="Visitenkarte Vorderseite">
  <div class="brand">
    <span class="brand-dot"></span>
    <span class="brand-name">F&amp;F Verwaltungsgesellschaft mbH</span>
  </div>
</section>

<section class="card card-back-dark" aria-label="Visitenkarte Rückseite dunkel">
  <div class="card-stack">
    <span class="brand-dot"></span>
    <span class="brand-name">F&amp;F Verwaltungsgesellschaft mbH</span>
  </div>
</section>

<section class="card card-back-light" aria-label="Visitenkarte Rückseite hell">
  <div class="card-stack">
    <span class="brand-dot"></span>
    <span class="brand-name">F&amp;F Verwaltungsgesellschaft mbH</span>
  </div>
</section>

</body>
</html>
```